Innovative Media Company needs Web Design

We need a web design for a new multimedia product that we are launching to potential partners and investors. The initial website we are looking to launch consists of three pages:
1.) A home/feature set page
2.) An account landing page
3.) An about us page
We would like the style of our website to be VERY similar to the following site: http://www.brintaro.com/tundra.
We have worked a bit on this project with a previous designer but were not happy with the results. As a guideline, you may refer to their previous work and the Tundra 88 website.
We realize this prize is a bit low for this project. However, there is a great opportunity for follow-on work. We are hoping to make a long-term business relationship with a high quality web-developer.
Attached are the product logo and our previous designer's work. Please let me know if you have any questions.
Thank you.
All,
Thanks for your submissions. Please note that rather than have headers that state "Enhanced TV Functionality" and "Seamless Device Integration", I would like to see all features (the six or seven boxes) in the same section. Also, please revise your designs to have the following statement below the picture that stretches across the screen and above the feature descriptions:
"Available via apps for the television and mobile devices,
naLix technology integrates numerous media components to provide users with
enhanced TV functionality and seamless device integration for an unparalleled
personalized viewing experience."
Thanks you.

```html
<!DOCTYPE html>
<html lang="en">
<head>
<meta charset="utf-8">
<title>naLix — About Us</title>
<link rel="stylesheet" href="https://fonts.googleapis.com/css2?family=Exo+2:wght@300;400;500&family=PT+Sans:wght@400;700&display=swap">
<style>
  :root {
    --page-bg: #ffffff;
    --top-rule: #d4d4d4;
    --ink: #2f2f2f;
    --ink-soft: #3c3c3c;
    --hero-dark: #181818;
    --hero-mid: #262626;
    --hero-text: #ffffff;
    --button-bg: #f1f1f1;
    --button-edge: #cfcfcf;
    --arrow: #bdbdbd;
    --frame-edge: #dedede;
    --footer-top: #2b2b2b;
    --footer-bottom: #3a3a3a;
    --footer-bar: #1f1f1f;
    --footer-text: #e6e6e6;
    --nav-divider: #d9d9d9;
  }
  * { box-sizing: border-box; margin: 0; padding: 0; }
  html, body { width: 866px; height: 1200px; overflow: hidden; background: var(--page-bg); }
  .page { position: relative; width: 866px; height: 1200px; overflow: hidden; font-family: "PT Sans", sans-serif; color: var(--ink); }

  /* Header */
  .site-header { position: absolute; left: 0; top: 0; width: 866px; height: 107px; border-top: 3px solid var(--top-rule); background: var(--page-bg); }
  .brand { position: absolute; left: 62px; top: 30px; display: flex; align-items: center; gap: 10px; }
  .brand-dot { width: 26px; height: 26px; border-radius: 50%; background: var(--ink-soft); }
  .brand-name { font-family: "Exo 2", sans-serif; font-weight: 500; font-size: 38px; color: var(--ink-soft); letter-spacing: 0.5px; }
  .main-nav { position: absolute; top: 56px; left: 0; width: 866px; }
  .main-nav a { position: absolute; font-family: "Exo 2", sans-serif; font-size: 14px; color: var(--ink); text-decoration: none; white-space: nowrap; }
  .nav-divider { position: absolute; top: 53px; width: 1px; height: 27px; background: var(--nav-divider); }

  /* Hero */
  .hero { position: absolute; left: 0; top: 107px; width: 866px; height: 382px; background: linear-gradient(180deg, var(--hero-dark) 0%, var(--hero-mid) 55%, var(--hero-dark) 100%); }
  .hero-screen { position: absolute; left: 63px; top: 55px; width: 375px; height: 270px; border-radius: 4px; background: linear-gradient(170deg, #3f4a36 0%, #6f7b63 45%, #2c3526 100%); }
  .hero-copy { position: absolute; left: 534px; top: 103px; color: var(--hero-text); font-family: "Exo 2", sans-serif; font-weight: 300; }
  .hero-kicker { font-size: 28px; line-height: 32px; }
  .hero-title { font-size: 40px; line-height: 38px; font-weight: 400; }
  .learn-more { position: absolute; left: 540px; top: 222px; width: 97px; height: 29px; border-radius: 3px; background: var(--button-bg); border: 1px solid var(--button-edge); font-family: "Exo 2", sans-serif; font-size: 15px; color: var(--ink); display: flex; align-items: center; justify-content: center; gap: 6px; text-decoration: none; }
  .slider-arrows { position: absolute; left: 781px; top: 339px; }

  /* Content */
  .about { position: absolute; left: 30px; top: 520px; width: 528px; }
  .section-title { font-family: "Exo 2", sans-serif; font-weight: 400; font-size: 21px; color: var(--ink); line-height: 28px; margin-bottom: 8px; }
  .subheading { margin-top: 12px; margin-bottom: 13px; }
  .body-text { font-size: 9.9px; line-height: 14.3px; text-align: justify; color: var(--ink-soft); }
  .body-text + .body-text { margin-top: 14.3px; }
  .body-text.tight { margin-top: 0; }
  .product-frame { position: absolute; left: 587px; top: 541px; width: 246px; height: 160px; border: 1px solid var(--frame-edge); background: var(--page-bg); }
  .product-shot { position: absolute; left: 19px; top: 13px; width: 206px; height: 134px; border-radius: 4px; background: linear-gradient(180deg, #6f9fcf 0%, #b7cfe0 40%, #d9643a 70%, #3e6b2a 100%); }

  /* Footer */
  .site-footer { position: absolute; left: 0; top: 1050px; width: 866px; height: 150px; background: linear-gradient(180deg, var(--footer-top), var(--footer-bottom)); color: var(--footer-text); }
  .footer-nav { position: absolute; left: 30px; top: 17px; display: flex; gap: 0; }
  .footer-nav a { font-size: 10px; color: var(--footer-text); text-decoration: none; margin-right: 33px; }
  .footer-address { position: absolute; right: 29px; top: 14px; text-align: right; font-size: 10px; line-height: 24px; }
  .footer-bar { position: absolute; left: 0; bottom: 0; width: 866px; height: 32px; background: var(--footer-bar); border-top: 1px solid #444; }
  .copyright { position: absolute; left: 24px; top: 9px; font-size: 10px; color: var(--footer-text); }
</style>
</head>
<body>
<div class="page">

  <header class="site-header">
    <div class="brand">
      <span class="brand-dot"></span>
      <span class="brand-name">naLix</span>
    </div>
    <nav class="main-nav">
      <a href="#" style="left:557px;">Home</a>
      <a href="#" style="left:633px;">Account Page</a>
      <a href="#" style="left:750px;">About Us</a>
    </nav>
    <span class="nav-divider" style="left:616px;"></span>
    <span class="nav-divider" style="left:724px;"></span>
  </header>

  <section class="hero">
    <div class="hero-screen" role="img" aria-label="Flat-screen television showing sunlight through a forest"></div>
    <div class="hero-copy">
      <p class="hero-kicker">Step into the</p>
      <h1 class="hero-title">Next Generation<br>of television</h1>
    </div>
    <a class="learn-more" href="#">learn more
      <svg width="6" height="10" viewBox="0 0 6 10"><path d="M1 1l4 4-4 4" fill="none" stroke="#2f2f2f" stroke-width="1.3"/></svg>
    </a>
    <svg class="slider-arrows" width="40" height="28" viewBox="0 0 40 28" aria-label="Slide controls">
      <path d="M12 2L2 14l10 12" fill="none" stroke="var(--arrow)" stroke-width="1.6"/>
      <path d="M28 2l10 12-10 12" fill="none" stroke="var(--arrow)" stroke-width="1.6"/>
    </svg>
  </section>

  <main class="about">
    <h2 class="section-title">Little About our Company</h2>
    <p class="body-text">Static website are the which are usually been used and are benefited through the Professionals and Small Companies. The companies with fewer budgets can promote their products and services through the static website and gain a lot.</p>
    <p class="body-text">To manage the static website HTML knowledge is the required. The simple website are also said as the static web as its embedded on a page.</p>
    <p class="body-text tight">Static website is a simple way to get your message out to the public. Static website are cheaper and also it needs less maintenance too. It's the simplest, cheapest and also the basic thing the search engine picks it up very easily. We at Brightline tech provide you the best simple websites too with total work done as using all the best designing and all done so that you can achieve the goal of yours through our work done on your website.</p>
    <p class="body-text">Sed ut perspiciatis unde omnis iste natus error sit voluptatem accusantium doloremque laudantium, totam rem aperiam, eaque ipsa quae ab illo inventore veritatis et quasi architecto beatae vitae dicta sunt explicabo. Nemo enim ipsam voluptatem quia voluptas sit aspernatur aut odit aut fugit, sed quia consequuntur magni dolores eos qui ratione voluptatem sequi nesciunt. Neque porro quisquam est, qui dolorem ipsum quia dolor sit amet, consectetur, adipisci velit, sed quia non numquam eius modi tempora incidunt ut labore et dolore magnam aliquam quaerat voluptatem. Ut enim ad minima veniam, quis nostrum exercitationem ullam corporis suscipit laboriosam, nisi ut aliquid ex ea</p>
    <h2 class="section-title subheading">Subheading</h2>
    <p class="body-text">Sed ut perspiciatis unde omnis iste natus error sit voluptatem accusantium doloremque laudantium, totam rem aperiam, eaque ipsa quae ab illo inventore veritatis et quasi architecto beatae vitae dicta sunt explicabo. Nemo enim ipsam voluptatem quia voluptas sit aspernatur aut odit aut fugit, sed quia consequuntur magni dolores eos qui ratione voluptatem sequi nesciunt. Neque porro quisquam est, qui dolorem ipsum quia dolor sit amet, consectetur, adipisci velit, sed quia non numquam eius modi tempora incidunt ut labore et dolore magnam aliquam quaerat voluptatem. Ut enim ad minima veniam, quis nostrum exercitationem ullam corporis suscipit laboriosam, nisi ut aliquid ex ea</p>
    <p class="body-text">Sed ut perspiciatis unde omnis iste natus error sit voluptatem accusantium doloremque laudantium, totam rem aperiam, eaque ipsa quae ab illo inventore veritatis et quasi architecto beatae vitae dicta sunt explicabo. Nemo enim ipsam voluptatem quia voluptas sit aspernatur aut odit aut fugit, sed quia consequuntur magni dolores eos qui ratione voluptatem sequi nesciunt. Neque porro quisquam est, qui dolorem ipsum quia dolor sit amet, consectetur, adipisci velit, sed quia non numquam eius modi tempora incidunt ut labore et dolore magnam aliquam quaerat voluptatem. Ut enim ad minima veniam, quis nostrum exercitationem ullam corporis suscipit laboriosam, nisi ut aliquid ex ea</p>
  </main>

  <figure class="product-frame">
    <div class="product-shot" role="img" aria-label="Television showing a field of tulips with a windmill"></div>
  </figure>

  <footer class="site-footer">
    <nav class="footer-nav">
      <a href="#">Home</a>
      <a href="#">Account Page</a>
      <a href="#">About Us</a>
      <a href="#">Products</a>
      <a href="#">Contact Us</a>
    </nav>
    <address class="footer-address" style="font-style:normal;">
      Address : XYZ Lorem Ipsum,<br>
      dummy text of the printing<br>
      industry.<br>
      Ph: 012 555 0143
    </address>
    <div class="footer-bar">
      <p class="copyright">© 2012 Company Name &nbsp;|&nbsp; All right reserved</p>
    </div>
  </footer>

</div>
</body>
</html>
```